Book cover for book about Climate Change

Looking for a clean, bold, and attractive cover for a mass-market paperback (5.5"x 8.5") about solving the climate change problem. Title is either "Where the Rivers Meet” or A Harbor Made of Glass” (your choice), subtitle is "A practical field guide to mending the weather — so that the young ones after us inherit steady seasons and open skies," author is Lorne Whitcombe. Thinking that it *might* feature an image of Earth (or a portion thereof) and its very thin layer of atmosphere -- but STRONGLY encourage other ideas too!

Requirements
Nice to have
• Keep it positive — NOT scary doom-and-gloom

```html
<!DOCTYPE html>
<html lang="en">
<head>
<meta charset="utf-8">
<title>A Harbor Made of Glass — Lorne Whitcombe</title>
<link rel="stylesheet" href="https://fonts.googleapis.com/css2?family=Poppins:wght@400;500;700;800&display=swap">
<style>
  :root {
    --page: #ffffff;
    --space-deep: #050b1c;
    --space-mid: #13295a;
    --space-glow: #24478a;
    --gold-edge: #e0a659;
    --gold-mid: #f2cf78;
    --gold-core: #fdf69c;
    --title-white: #ffffff;
    --subtitle: #f6eec0;
    --rule: #e8ecf5;
    --planet-ocean: #2c4f7a;
    --planet-land: #9a7a3e;
    --planet-halo: #fff4d6;
  }
  html, body {
    margin: 0;
    padding: 0;
    width: 1200px;
    height: 1200px;
    overflow: hidden;
    background: var(--page);
  }
  .canvas {
    position: relative;
    width: 1200px;
    height: 1200px;
  }
  .book-cover {
    position: absolute;
    left: 251px;
    top: 61px;
    width: 697px;
    height: 1077px;
    display: block;
  }
  .title-small {
    font-family: 'Poppins', sans-serif;
    font-weight: 700;
    fill: var(--title-white);
  }
  .title-large {
    font-family: 'Poppins', sans-serif;
    font-weight: 800;
  }
  .subtitle {
    font-family: 'Poppins', sans-serif;
    font-weight: 400;
    font-size: 21.5px;
    fill: var(--subtitle);
  }
  .author {
    font-family: 'Poppins', sans-serif;
    font-weight: 700;
    font-size: 31px;
    fill: var(--title-white);
    letter-spacing: 14px;
  }
  .title-rule {
    stroke: var(--rule);
    stroke-width: 2;
  }
</style>
</head>
<body>
<div class="canvas">
  <svg class="book-cover" viewBox="0 0 697 1077" xmlns="http://www.w3.org/2000/svg">
    <defs>
      <radialGradient id="space-gradient" cx="50%" cy="55%" r="75%">
        <stop offset="0%" stop-color="var(--space-glow)"/>
        <stop offset="50%" stop-color="var(--space-mid)"/>
        <stop offset="100%" stop-color="var(--space-deep)"/>
      </radialGradient>
      <linearGradient id="gold-gradient" x1="0" y1="0" x2="1" y2="0">
        <stop offset="0%" stop-color="var(--gold-edge)"/>
        <stop offset="30%" stop-color="var(--gold-mid)"/>
        <stop offset="50%" stop-color="var(--gold-core)"/>
        <stop offset="72%" stop-color="var(--gold-mid)"/>
        <stop offset="100%" stop-color="var(--gold-edge)"/>
      </linearGradient>
      <radialGradient id="halo-gradient" cx="50%" cy="45%" r="50%">
        <stop offset="60%" stop-color="var(--planet-halo)" stop-opacity="0.9"/>
        <stop offset="78%" stop-color="#e7b7c4" stop-opacity="0.35"/>
        <stop offset="100%" stop-color="#e7b7c4" stop-opacity="0"/>
      </radialGradient>
      <radialGradient id="planet-gradient" cx="40%" cy="40%" r="65%">
        <stop offset="0%" stop-color="var(--planet-ocean)"/>
        <stop offset="55%" stop-color="#3f5d72"/>
        <stop offset="85%" stop-color="var(--planet-land)"/>
        <stop offset="100%" stop-color="#c7a96a"/>
      </radialGradient>
    </defs>

    <rect class="space-backdrop" width="697" height="1077" fill="url(#space-gradient)" role="img" aria-label="Deep blue starfield backdrop"/>

    <g class="title-block">
      <line class="title-rule" x1="59" y1="79" x2="320" y2="79"/>
      <line class="title-rule" x1="377" y1="79" x2="636" y2="79"/>
      <text class="title-small" x="348.5" y="96" font-size="46" text-anchor="middle">A</text>

      <text class="title-large" x="347" y="218" font-size="158" text-anchor="middle"
            textLength="578" lengthAdjust="spacingAndGlyphs" fill="url(#gold-gradient)">HARBOR</text>

      <line class="title-rule" x1="59" y1="247" x2="245" y2="247"/>
      <line class="title-rule" x1="452" y1="247" x2="636" y2="247"/>
      <text class="title-small" x="348.5" y="264" font-size="46" text-anchor="middle"
            textLength="190" lengthAdjust="spacingAndGlyphs">MADE OF</text>

      <text class="title-large" x="348" y="369" font-size="138" text-anchor="middle"
            textLength="579" lengthAdjust="spacingAndGlyphs" fill="url(#gold-gradient)">GLASS</text>
    </g>

    <g class="subtitle-block">
      <text class="subtitle" x="348.5" y="420" text-anchor="middle">A practical field guide to mending the weather</text>
      <text class="subtitle" x="348.5" y="451" text-anchor="middle">— so that the young ones after us inherit</text>
      <text class="subtitle" x="348.5" y="482" text-anchor="middle">steady seasons and open skies</text>
    </g>

    <g class="planet" role="img" aria-label="Glowing Earth with a thin bright atmosphere, sunrise over the horizon">
      <circle cx="354" cy="746" r="186" fill="url(#halo-gradient)"/>
      <circle cx="354" cy="746" r="124" fill="url(#planet-gradient)"/>
    </g>

    <text class="author" x="355" y="1032" text-anchor="middle">LORNE WHITCOMBE</text>
  </svg>
</div>
</body>
</html>
```